Professional Package for CPA Firm

We would like a stationery design for our new CPA Firm based in Atlanta, GA called 'Vale 8'. We work with investors to help grow investments, tax free. We would like the design to have a professional/minimal look with a 'wow' factor. We need 9.5″ x 4.125″, 9x12, and 10x13 mailing envelopes, business cards, and a letterhead. We have a logo that is already complete. For the letterhead, we would like to have space to put credentials at the bottom of the page

Industry/Entity Type

CPA, Accounting

```html
<!DOCTYPE html>
<html lang="en">
<head>
<meta charset="utf-8">
<title>Vale 8 Stationery</title>
<link href="https://fonts.googleapis.com/css2?family=Montserrat:wght@400;500;700;800&family=Open+Sans:wght@400;600&display=swap" rel="stylesheet">
<style>
:root{
  --bg:#e9e9e9;
  --paper:#f3f3f3;
  --ink:#1f2022;
  --text:#4a4a4a;
  --blue:#2a95c9;
  --folder:#1b1c1e;
  --card-dark:#353535;
  --muted:#9a9a9a;
}
*{margin:0;padding:0;box-sizing:border-box}
html,body{width:1200px;height:795px;overflow:hidden;background:var(--bg)}
body{position:relative;font-family:"Open Sans",Arial,sans-serif;color:var(--text)}
.piece{position:absolute}

/* brand lockup */
.brand{display:flex;align-items:center;gap:4px;font-family:"Montserrat",Arial,sans-serif;font-weight:800;color:var(--ink);white-space:nowrap}
.brand-square{background:var(--blue);flex:none}
.brand-sub{font-family:"Montserrat",Arial,sans-serif;font-weight:500;color:var(--ink);white-space:nowrap}

/* letterhead */
.letterhead{left:292px;top:99px;width:294px;height:415px;background:var(--paper)}
.letterhead .brand{position:absolute;left:26px;top:50px;font-size:11px}
.letterhead .brand-square{width:8px;height:8px}
.letterhead .brand-sub{position:absolute;left:26px;top:64px;font-size:3.3px;letter-spacing:.2px}
.lh-contact{position:absolute;left:205px;top:32px;font-size:5.6px;line-height:7.7px;list-style:none;color:var(--text)}
.lh-contact li{display:flex;align-items:center;gap:2px}
.lh-contact svg{width:5px;height:5px;flex:none}
.lh-body{position:absolute;left:26px;top:97px;width:241px;font-size:5.3px;line-height:8px}
.lh-body p{text-align:justify;margin-bottom:8px}
.lh-body .salute{margin-bottom:8px}
.lh-signature{position:absolute;left:27px;top:307px;width:34px;height:32px;background:linear-gradient(135deg,#e6e6e6,#dcdcdc);border-radius:3px}
.lh-footer{position:absolute;left:0;right:0;top:385px;text-align:center;font-size:5.7px;line-height:7.2px;color:#555}

/* folder */
.folder{left:637px;top:80px;width:346px;height:437px;background:var(--folder)}
.folder-fold{position:absolute;left:17px;top:0;width:1px;height:100%;background:#2b2c2f}
.folder-lockup{position:absolute;left:0;right:0;top:150px;display:flex;flex-direction:column;align-items:center}
.folder-mark{width:56px;height:56px;background:var(--blue);margin-bottom:16px}
.folder-name{font-family:"Montserrat",Arial,sans-serif;font-weight:800;font-size:52px;line-height:52px;color:#f1f1f1;letter-spacing:1px}
.folder-sub{font-family:"Montserrat",Arial,sans-serif;font-weight:400;font-size:14.5px;color:#f1f1f1;letter-spacing:2.2px;margin-top:6px}
.folder-band{position:absolute;left:0;right:0;top:404px;height:15px;background:var(--blue);text-align:center;font-family:"Montserrat",Arial,sans-serif;font-weight:500;font-size:7.6px;line-height:15px;color:#fff;letter-spacing:.3px}

/* business cards */
.card-front{left:187px;top:550px;width:132px;height:75px;background:var(--paper)}
.card-front .brand{position:absolute;left:18px;top:32px;font-size:9px}
.card-front .brand-square{width:6px;height:6px}
.card-front .brand-sub{position:absolute;left:19px;top:44px;font-size:2.8px}
.card-divider{position:absolute;left:63px;top:21px;width:.8px;height:33px;background:var(--ink)}
.card-details{position:absolute;left:69px;top:21px;font-size:3.3px;line-height:4.3px;color:#444}
.card-name{font-family:"Montserrat",Arial,sans-serif;font-weight:700;font-size:4.2px;color:var(--ink)}
.card-role{color:var(--blue);font-weight:600;margin-bottom:2px}
.card-back{left:187px;top:647px;width:132px;height:74px;background:var(--card-dark);display:flex;flex-direction:column;align-items:center;justify-content:center}
.card-back .brand{color:#a8a8a8;font-size:14px}
.card-back .brand-square{width:9px;height:9px}
.card-back .brand-sub{color:#a8a8a8;font-size:4px;letter-spacing:.4px;margin-top:2px}

/* envelopes */
.envelope-front{left:353px;top:561px;width:329px;height:157px;background:var(--paper)}
.envelope-front .lockup{position:absolute;left:22px;top:52px;width:68px;display:flex;flex-direction:column;align-items:center}
.envelope-front .brand{font-size:14px}
.envelope-front .brand-square{width:9px;height:9px}
.envelope-front .brand-sub{font-size:4.4px;letter-spacing:.3px;margin-top:1px}
.envelope-address{font-size:5.4px;line-height:6.6px;text-align:center;color:#444;margin-top:3px;white-space:nowrap}
.envelope-back{left:714px;top:561px;width:328px;height:157px;background:var(--paper)}
.envelope-flap{position:absolute;left:0;top:0;width:100%;height:50px;background:var(--folder);clip-path:polygon(0 0,100% 0,98.2% 100%,1.8% 100%);display:flex;flex-direction:column;align-items:center;justify-content:center}
.envelope-flap .brand{color:#fff;font-size:9px}
.envelope-flap .brand-square{width:6px;height:6px}
.envelope-flap .brand-sub{color:#fff;font-size:2.6px;margin-top:1px}
</style>
</head>
<body>

<section class="piece letterhead">
  <div class="brand"><span class="brand-square"></span>Vale 8</div>
  <div class="brand-sub">CPAs and Tax Advisors</div>
  <ul class="lh-contact">
    <li><svg viewBox="0 0 10 10"><path d="M2 1l2 2-1 1.5c.6 1.2 1.4 2 2.6 2.6L7 6l2 2-1.4 1.4C4.5 9 1 5.5.6 2.4z" fill="#2a95c9"/></svg>+1 404 555 0187</li>
    <li><svg viewBox="0 0 10 10"><rect x="2.5" y="1" width="5" height="3" fill="none" stroke="#2a95c9"/><rect x="1" y="4" width="8" height="4" fill="#2a95c9"/><rect x="3" y="6" width="4" height="3" fill="#fff" stroke="#2a95c9" stroke-width=".6"/></svg>404.555.0192</li>
    <li><svg viewBox="0 0 10 10"><rect x="1" y="2" width="8" height="6" fill="#2a95c9"/><path d="M1 2l4 3.5L9 2" fill="none" stroke="#fff" stroke-width=".8"/></svg>info@valeeight.com</li>
    <li><svg viewBox="0 0 10 10"><circle cx="5" cy="5" r="4" fill="none" stroke="#2a95c9"/><path d="M1 5h8M5 1c-2 2.5-2 5.5 0 8M5 1c2 2.5 2 5.5 0 8" fill="none" stroke="#2a95c9" stroke-width=".7"/></svg>www.valeeight.com</li>
  </ul>
  <div class="lh-body">
    <p class="salute">Dear customer,</p>
    <p>Lorem ipsum dolor sit amet, consectetur adipisicing elit, sed do eiusmod tempor incididunt ut labore et dolore magna aliqua. Ut enim ad minim veniam, quis nostrud exercitation ullamco laboris nisi ut aliquip ex ea commodo consequat. Duis aute irure dolor in reprehenderit in voluptate velit esse cillum dolore eu fugiat nulla pariatur. Excepteur sint occaecat cupidatat non proident, sunt in culpa qui officia deserunt mollit anim id est laborum.</p>
    <p>Lorem ipsum dolor sit amet, consectetur adipisicing elit, sed do eiusmod tempor incididunt ut labore et dolore magna aliqua. Ut enim ad minim veniam, quis nostrud exercitation ullamco laboris nisi ut aliquip ex ea commodo consequat. Duis aute irure dolor in reprehenderit in voluptate velit esse cillum dolore eu fugiat nulla pariatur. Excepteur sint occaecat cupidatat non proident, sunt in culpa qui officia deserunt mollit anim id est laborum.</p>
    <p>Lorem ipsum dolor sit amet, consectetur adipisicing elit, sed do eiusmod tempor incididunt ut labore et dolore magna aliqua. Ut enim ad minim veniam, quis nostrud exercitation ullamco laboris nisi ut aliquip ex ea commodo consequat. Duis aute irure dolor in reprehenderit in voluptate velit esse cillum dolore eu fugiat nulla pariatur. Excepteur sint occaecat cupidatat non proident, sunt in culpa qui officia deserunt mollit anim id est laborum.</p>
    <p>Lorem ipsum dolor sit amet, consectetur adipisicing elit, sed do eiusmod tempor incididunt ut labore et dolore magna aliqua. Ut enim ad minim veniam, quis nostrud exercitation ullamco laboris nisi ut aliquip ex ea commodo consequat. Duis aute irure dolor in reprehenderit.</p>
    <p class="salute">Yours Sincerely,</p>
  </div>
  <div class="lh-signature" role="img" aria-label="Handwritten signature"></div>
  <div class="lh-footer">Vale 8 CPAs and Tax Advisors<br>48 Linden Crest Road, Marietta, GA 30062</div>
</section>

<section class="piece folder">
  <div class="folder-fold"></div>
  <div class="folder-lockup">
    <div class="folder-mark"></div>
    <div class="folder-name">Vale 8</div>
    <div class="folder-sub">CPAs and Tax Advisors</div>
  </div>
  <div class="folder-band">www.valeeight.com</div>
</section>

<section class="piece card-front">
  <div class="brand"><span class="brand-square"></span>Vale 8</div>
  <div class="brand-sub">CPAs and Tax Advisors</div>
  <div class="card-divider"></div>
  <div class="card-details">
    <div class="card-name">MARCUS HOLLARD</div>
    <div class="card-role">Managing Director</div>
    <div>48 Linden Crest Road,<br>Marietta, GA 30062</div>
    <div>+1 404 555 0187</div>
    <div>info@valeeight.com</div>
    <div>www.valeeight.com</div>
  </div>
</section>

<section class="piece card-back">
  <div class="brand"><span class="brand-square"></span>Vale 8</div>
  <div class="brand-sub">CPAs and Tax Advisors</div>
</section>

<section class="piece envelope-front">
  <div class="lockup">
    <div class="brand"><span class="brand-square"></span>Vale 8</div>
    <div class="brand-sub">CPAs and Tax Advisors</div>
    <div class="envelope-address">48 Linden Crest Road,<br>Marietta, GA 30062</div>
  </div>
</section>

<section class="piece envelope-back">
  <div class="envelope-flap">
    <div class="brand"><span class="brand-square"></span>Vale 8</div>
    <div class="brand-sub">CPAs and Tax Advisors</div>
  </div>
</section>

</body>
</html>
```